Bring me business with this creative business card

Design my new business card. I am looking for something different with an impact. People will take a look at this card & they will 1- see how different & creative I am, 2-understand what I do 3- Call me to meet me!

I make videos with a message, testimonials. I am dynamic, fun, creative & human. My new website is in construction but in the meantime you can check this old one: brightpath.ca & another one Tidebloom.com & tidebloom facebook page.
I make videos. sometimes with a cameraman, sometimes with my phone. As an ex Public Relations agent, the message is the most important thing for me. I want to make my clients shine! When they start with me they often remind me of a lamb, when I finish coaching them they are powerful like LIONS! That's why I need a powerful business card!

Target Market(s)

Entrepreneurs, solo entrepreneurs, small & medium companies & start ups. People i will meet while networking. People that need videos on their website & social Networks to get attention, to be visible. men & women. From 35 to 49 years old.
I am an ex Public relations agent. I used to send clients in traditional medias, now with videos they have more chances to be seen on google the new media. I do videos of the president, his team, his loyal clients saying how great the company is & expert videos like series so people can be seen for example every 1 st of every month with a short 2 minute video. Also with my 20 years in marketing & communications I can coach & give tips to anybody who needs it.
Target: anybody who would like my old website brightpath.ca & I also have another website but it will be off line soon: tidebloom.com could give you ideas.

Industry/Entity Type

Communications

Contact Information for Business Card

I am in Montreal,So the business cards have to be the usual size like we have in Montreal: 9 cm x 5 cm
Details:My text: Mathilde Tessier Communication coach/Chief Lion. "Creating Videos as unique as you" off: 514-555-0147 cell: 514-555-0183. tidebloom.com
mathilde@tidebloom.com logo facebook, youtube, instagram

Colors
f37122

Requirements
Must have
• Dynamic, happy. Orange. Be creative in the look but NOT the shape of the card. Easy to read. Big enough to read.
Should not have
• No funny shapes: no round, no square, just the usual. I love creative but NOT on shape.

```html
<!DOCTYPE html>
<html lang="en">
<head>
<meta charset="utf-8">
<title>Tidebloom business card</title>
<link href="https://fonts.googleapis.com/css2?family=Roboto+Condensed:wght@400;700&display=swap" rel="stylesheet">
<style>
  :root {
    --orange: #f37122;
    --orange-deep: #eb5a24;
    --orange-soft: #f5a13a;
    --paper: #ffffff;
    --backdrop: #ece9e4;
    --ink-light: #ffffff;
  }
  * { box-sizing: border-box; margin: 0; padding: 0; }
  html, body { width: 1200px; height: 911px; overflow: hidden; }
  body {
    background: var(--backdrop);
    font-family: "Roboto Condensed", "Arial Narrow", sans-serif;
    position: relative;
  }
  .card {
    position: absolute;
    left: 290px;
    width: 620px;
    height: 344px;
    background: var(--paper);
    box-shadow: 0 6px 18px rgba(0,0,0,.18);
    overflow: hidden;
  }
  .card--front { top: 96px; }
  .card--back { top: 472px; }

  /* front */
  .front-band {
    position: absolute; left: 0; top: 0; bottom: 0; width: 330px;
    background: linear-gradient(90deg, var(--orange-deep), var(--orange));
    display: flex; align-items: center; padding: 0 22px;
    color: var(--ink-light);
  }
  .identity { text-align: right; padding-right: 16px; border-right: 1px solid rgba(255,255,255,.6); }
  .identity__name { font-weight: 700; font-size: 21px; letter-spacing: .5px; }
  .identity__role { font-size: 13px; letter-spacing: .4px; line-height: 1.35; text-transform: uppercase; }
  .contacts { list-style: none; padding-left: 14px; font-size: 13px; line-height: 1.75; }
  .contacts li { display: flex; align-items: center; gap: 7px; white-space: nowrap; }
  .contacts svg { width: 11px; height: 11px; flex: none; }

  .brand {
    position: absolute; left: 330px; right: 0; top: 0; bottom: 0;
    display: flex; align-items: center; justify-content: center; gap: 12px;
  }
  .brand__dot { width: 34px; height: 34px; border-radius: 50%; background: var(--orange); }
  .brand__name { font-size: 36px; font-weight: 700; letter-spacing: 2px; color: var(--orange); }

  /* back */
  .tagline {
    position: absolute; left: 38px; top: 50%;
    transform: translate(-50%, -50%) rotate(90deg);
    transform-origin: center;
    margin-left: 10px;
    white-space: nowrap; font-size: 14px; font-weight: 700;
    color: var(--orange);
  }
  .back-brand {
    position: absolute; inset: 0;
    display: flex; align-items: center; justify-content: center; gap: 14px;
  }
  .back-brand .brand__dot { width: 44px; height: 44px; }
  .back-brand .brand__name { font-size: 44px; }
  .socials { position: absolute; right: 22px; bottom: 22px; display: flex; flex-direction: column; gap: 6px; }
  .socials span { width: 16px; height: 16px; border-radius: 50%; background: var(--orange); display: block; }
</style>
</head>
<body>

<section class="card card--front">
  <div class="front-band">
    <div class="identity">
      <p class="identity__name">MATHILDE T.</p>
      <p class="identity__role">Communication coach<br>Chief Lion</p>
    </div>
    <ul class="contacts">
      <li><svg viewBox="0 0 12 12"><path fill="#fff" d="M3 1l2 2.5-1 1.2a7 7 0 003.3 3.3l1.2-1L11 9l-1 2C5 11 1 7 1 2z"/></svg>514-555-0147</li>
      <li><svg viewBox="0 0 12 12"><rect x="3" y="1" width="6" height="10" rx="1" fill="none" stroke="#fff" stroke-width="1.3"/></svg>514-555-0183</li>
      <li><svg viewBox="0 0 12 12"><rect x="1" y="2.5" width="10" height="7" fill="#fff"/><path d="M1 2.5l5 4 5-4" fill="none" stroke="#eb5a24" stroke-width="1"/></svg>mathilde@tidebloom.com</li>
      <li><svg viewBox="0 0 12 12"><circle cx="6" cy="6" r="5" fill="#fff"/><circle cx="6" cy="6" r="2" fill="#eb5a24"/></svg>www.tidebloom.com</li>
    </ul>
  </div>
  <div class="brand">
    <span class="brand__dot"></span>
    <span class="brand__name">TIDEBLOOM</span>
  </div>
</section>

<section class="card card--back">
  <p class="tagline">Creating Videos as unique as you</p>
  <div class="back-brand">
    <span class="brand__dot"></span>
    <span class="brand__name">TIDEBLOOM</span>
  </div>
  <div class="socials" aria-label="Social network links">
    <span></span><span></span><span></span>
  </div>
</section>

</body>
</html>
```